Redesign of business card for Cedar Ridge Mechanical

We are looking for a new design for our business cards for Cedar Ridge Mechanical. We are a plumbing & HVAC construction company, operating on the West Coast of Canada and USA. Logo attached.
Industry/Entity Type
Construction - Plumbing & HVAC
Contact Information for Business Card
Name, address, phone numbers, email, website address
Look and feel
Each slider illustrates characteristics of the customer's brand and the style your logo design should communicate.

```html
<!DOCTYPE html>
<html lang="en">
<head>
<meta charset="utf-8">
<title>Cedar Ridge Mechanical – Business Card</title>
<link href="https://fonts.googleapis.com/css2?family=Bebas+Neue&family=Roboto:wght@400&display=swap" rel="stylesheet">
<style>
  :root {
    --backdrop: #ababab;
    --card-light: #ffffff;
    --card-dark: #000000;
    --ink: #231f20;
    --ink-soft: #2b2b2b;
    --paper: #ffffff;
    --rule: #9a9a9a;
  }
  html, body {
    margin: 0;
    padding: 0;
    width: 1093px;
    height: 1200px;
    overflow: hidden;
    background: var(--backdrop);
  }
  .canvas {
    position: relative;
    width: 1093px;
    height: 1200px;
  }
  .card {
    position: absolute;
    left: 265px;
    width: 578px;
    height: 357px;
    border-radius: 27px;
    overflow: hidden;
  }
  .card--front { top: 226px; background: var(--card-light); }
  .card--back  { top: 621px; background: var(--card-dark); }

  .brand {
    position: absolute;
    display: flex;
    align-items: center;
    font-family: "Bebas Neue", sans-serif;
    font-weight: 400;
    line-height: 0.92;
    letter-spacing: 0.5px;
  }
  .brand__mark { flex: none; }
  .brand__name { margin: 0; }

  .card--front .brand {
    left: 70px;
    top: 132px;
    gap: 12px;
    color: var(--ink);
    font-size: 34px;
  }
  .card--front .brand__mark {
    width: 40px; height: 40px; background: var(--ink);
  }

  .card--back .brand {
    left: 0; right: 0;
    top: 118px;
    justify-content: center;
    gap: 22px;
    color: var(--paper);
    font-size: 66px;
  }
  .card--back .brand__mark {
    width: 76px; height: 76px; background: var(--paper);
  }

  .divider {
    position: absolute;
    left: 288px;
    top: 75px;
    width: 1px;
    height: 208px;
    background: var(--rule);
  }

  .contact {
    position: absolute;
    left: 311px;
    top: 88px;
    font-family: "Roboto", sans-serif;
    color: var(--ink-soft);
  }
  .contact__name {
    margin: 0;
    font-family: "Bebas Neue", sans-serif;
    font-weight: 400;
    font-size: 33px;
    line-height: 1;
    color: var(--ink);
    letter-spacing: 0.2px;
  }
  .contact__role {
    margin: -2px 0 0;
    font-size: 16.5px;
    line-height: 1.2;
  }
  .contact__list {
    list-style: none;
    margin: 13px 0 0;
    padding: 0;
  }
  .contact__item {
    display: flex;
    align-items: center;
    gap: 7px;
    font-size: 16.5px;
    line-height: 21px;
  }
  .contact__icon { width: 15px; height: 15px; flex: none; fill: var(--ink); }
  .contact__address {
    margin: 13px 0 0;
    font-style: normal;
    font-size: 16.5px;
    line-height: 21px;
  }
</style>
</head>
<body>
<main class="canvas">

  <section class="card card--front" aria-label="Business card front">
    <div class="brand">
      <span class="brand__mark"></span>
      <p class="brand__name">Cedar Ridge<br>Mechanical</p>
    </div>

    <div class="divider"></div>

    <div class="contact">
      <h1 class="contact__name">Marcus Reed</h1>
      <p class="contact__role">Managing Director</p>
      <ul class="contact__list">
        <li class="contact__item">
          <svg class="contact__icon" viewBox="0 0 16 16" aria-hidden="true"><path d="M3.6 1.2l2.3 2.6c.3.4.3.9 0 1.2L4.7 6.3c.8 1.9 2.9 4.1 5 5l1.3-1.2c.3-.3.9-.3 1.2 0l2.6 2.3c.4.3.4.9 0 1.3l-1.3 1.3c-.6.6-1.5.8-2.3.5C6.8 14 2 9.2.5 4.8.2 4 .4 3.1 1 2.5L2.3 1.2c.4-.4 1-.4 1.3 0z"/><path d="M9.5 1a6 6 0 0 1 5.5 5.5h-1.3A4.7 4.7 0 0 0 9.5 2.3zM9.5 3.7a3.3 3.3 0 0 1 2.8 2.8H11a2 2 0 0 0-1.5-1.5z"/></svg>
          044-123 456 789
        </li>
        <li class="contact__item">
          <svg class="contact__icon" viewBox="0 0 16 16" aria-hidden="true"><path d="M0 3h16v10H0z M1.3 4.2v.3L8 9l6.7-4.5v-.3z" fill-rule="evenodd"/></svg>
          info@webname.com
        </li>
        <li class="contact__item">
          <svg class="contact__icon" viewBox="0 0 16 16" aria-hidden="true"><path fill-rule="evenodd" d="M8 .5a7.5 7.5 0 1 1 0 15 7.5 7.5 0 0 1 0-15zm-.7 1.5C6.1 3.3 5.5 5 5.4 7.3h1.9zm1.4 0v5.3h1.9C10.5 5 9.9 3.3 8.7 2zM6 2.3A6 6 0 0 0 2 7.3h2.1c.1-2 .7-3.7 1.9-5zm4 0c1.2 1.3 1.8 3 1.9 5H14a6 6 0 0 0-4-5zM2 8.7a6 6 0 0 0 4 5c-1.2-1.3-1.8-3-1.9-5zm3.4 0c.1 2.3.7 4 1.9 5.3V8.7zm3.3 0V14c1.2-1.3 1.8-3 1.9-5.3zm3.2 0c-.1 2-.7 3.7-1.9 5a6 6 0 0 0 4-5z"/></svg>
          www.websitename.com
        </li>
      </ul>
      <address class="contact__address">421, Address line goes here<br>45452,Country Name</address>
    </div>
  </section>

  <section class="card card--back" aria-label="Business card back">
    <div class="brand">
      <span class="brand__mark"></span>
      <p class="brand__name">Cedar Ridge<br>Mechanical</p>
    </div>
  </section>

</main>
</body>
</html>
```